BrindleStaffing Business Card Design

We are a staffing company finding positions for dedicated nurses and physicians.

Target Market(s)

Business Professionals

Industry/Entity Type

Staffing

Contact Information for Business Card

Gordon Pratley
Chairman
417 39th Avenue South
SAINT PETERSBURG FL 33712
813-555-4172 Mobile
813-555-8036 Fax
gpratley@brindlestaffing.com
www.brindlestaffing.com

Font styles to use
Sans Serif

Colors
fbee3e
f04a50
f37122

Requirements
Must have
• Logo Attached, see colors below. We'd like to see Yellow, Orange and Red.

```html
<!DOCTYPE html>
<html lang="en">
<head>
<meta charset="utf-8">
<title>BrindleStaffing Business Card</title>
<link rel="stylesheet" href="https://fonts.googleapis.com/css2?family=Open+Sans:wght@400;600;700&display=swap">
<style>
  :root {
    --canvas-bg: #e9e7e3;
    --card-white: #ffffff;
    --brand-yellow: #fbee3e;
    --brand-red: #f04a50;
    --brand-orange: #f37122;
    --text-white: #ffffff;
    --card-shadow: 0 10px 28px rgba(0,0,0,0.22);
  }
  * { margin: 0; padding: 0; box-sizing: border-box; }
  html, body { width: 1200px; height: 768px; overflow: hidden; }
  body {
    background: var(--canvas-bg);
    font-family: "Open Sans", Arial, sans-serif;
    position: relative;
  }
  .card {
    position: absolute;
    top: 234px;
    width: 525px;
    height: 300px;
    border-radius: 20px;
    overflow: hidden;
    box-shadow: var(--card-shadow);
  }
  .card-front { left: 50px; background: var(--card-white); }
  .card-back { left: 625px; background: var(--brand-orange); display: flex; align-items: center; justify-content: center; }

  .accent-strip {
    position: absolute;
    left: 0; top: 80px;
    width: 9px; height: 220px;
    background: var(--brand-yellow);
  }
  .front-logo {
    position: absolute;
    left: 38px; top: 160px;
    display: flex; align-items: center; gap: 8px;
  }
  .logo-name {
    font-weight: 700;
    font-size: 27px;
    letter-spacing: -0.5px;
    color: var(--brand-orange);
    white-space: nowrap;
  }
  .logo-dot {
    width: 12px; height: 12px; border-radius: 50%;
    background: var(--brand-red);
  }
  .contact-panel {
    position: absolute;
    right: 0; top: 48px;
    width: 228px; height: 204px;
    background: var(--brand-red);
    color: var(--text-white);
    padding: 20px 14px 0 22px;
  }
  .contact-name { font-weight: 700; font-size: 17px; line-height: 1.15; white-space: nowrap; }
  .contact-title { font-weight: 600; font-size: 11.5px; margin-bottom: 10px; }
  .contact-address { font-size: 11px; line-height: 1.4; margin-bottom: 8px; white-space: nowrap; }
  .contact-list { list-style: none; font-size: 11px; line-height: 1.55; }
  .contact-list li { display: flex; align-items: center; gap: 7px; white-space: nowrap; }
  .contact-list svg { width: 10px; height: 10px; flex: none; }

  .back-logo { display: flex; align-items: center; gap: 12px; }
  .back-logo .logo-name { color: var(--text-white); font-size: 46px; letter-spacing: -1px; }
  .back-logo .logo-dot { background: var(--brand-yellow); width: 18px; height: 18px; }
</style>
</head>
<body>
  <section class="card card-front" aria-label="Business card front">
    <div class="accent-strip"></div>
    <div class="front-logo">
      <span class="logo-name">BrindleStaffing</span>
      <span class="logo-dot"></span>
    </div>
    <div class="contact-panel">
      <p class="contact-name">Gordon Pratley</p>
      <p class="contact-title">Chairman</p>
      <p class="contact-address">417 39th Avenue South<br>Saint Petersburg Fl 33712</p>
      <ul class="contact-list">
        <li>
          <svg viewBox="0 0 10 10"><rect x="2" y="0.5" width="6" height="9" rx="1" fill="none" stroke="#fff" stroke-width="1.2"/></svg>
          813-555-4172
        </li>
        <li>
          <svg viewBox="0 0 10 10"><rect x="0.5" y="3" width="9" height="6" fill="#fff"/><rect x="2.5" y="0.5" width="5" height="3" fill="none" stroke="#fff"/></svg>
          813-555-8036
        </li>
        <li>
          <svg viewBox="0 0 10 10"><rect x="0.5" y="1.5" width="9" height="7" fill="#fff"/><path d="M0.5 1.5 L5 5.5 L9.5 1.5" fill="none" stroke="#f04a50" stroke-width="1"/></svg>
          gpratley@brindlestaffing.com
        </li>
        <li>
          <svg viewBox="0 0 10 10"><circle cx="5" cy="5" r="4.5" fill="#fff"/><path d="M0.5 5 H9.5 M5 0.5 V9.5" stroke="#f04a50" stroke-width="0.9"/></svg>
          www.brindlestaffing.com
        </li>
      </ul>
    </div>
  </section>

  <section class="card card-back" aria-label="Business card back">
    <div class="back-logo">
      <span class="logo-name">BrindleStaffing</span>
      <span class="logo-dot"></span>
    </div>
  </section>
</body>
</html>
```